TALMORK

The business want a professional looking business card. We have a scetch we will add but want the extra upgrade, and would like more suggestions for variations of our business cards.

```html
<!DOCTYPE html>
<html lang="en">
<head>
<meta charset="utf-8">
<title>TALMORK – Business Card Options</title>
<link href="https://fonts.googleapis.com/css2?family=Cinzel:wght@400;500;600&family=Cormorant+Garamond:wght@500;600&family=Montserrat:wght@400;500&display=swap" rel="stylesheet">
<style>
  :root {
    --gold: #b8902f;
    --gold-light: #d4ae55;
    --paper: #f1ebe0;
    --paper-warm: #efe7da;
    --ink-dark: #1c1b1a;
    --bg-sand: #e6d8c3;
    --bg-slate: #4a4744;
    --bg-cream: #eadcc8;
    --accent-sand: #dcc9ad;
    --caption: #3a2f22;
    --caption-light: #efe7da;
    --canvas: #ffffff;
  }
  * { box-sizing: border-box; margin: 0; padding: 0; }
  html, body { width: 1200px; height: 927px; overflow: hidden; background: var(--canvas); }
  .board { position: relative; width: 1200px; height: 927px; }
  .option {
    position: absolute; top: 74px; width: 399px; height: 799px; overflow: hidden;
  }
  .option--minimal { left: 0; background: linear-gradient(180deg, #e4d5bf 0%, #eadfce 100%); }
  .option--dark { left: 401px; background: linear-gradient(180deg, #3f3d3b 0%, #5a5652 70%, #d9cdbd 100%); }
  .option--modern { left: 802px; width: 398px; background: linear-gradient(180deg, #e6d6c0 0%, #efe4d4 100%); }

  .card { position: absolute; left: 40px; width: 320px; overflow: hidden; box-shadow: 0 6px 14px rgba(0,0,0,.18); }
  .card--front { top: 150px; height: 196px; }
  .card--back { top: 400px; height: 200px; left: 30px; width: 340px; }
  .option--minimal .card, .option--modern .card { background: var(--paper); }
  .option--dark .card { background: var(--ink-dark); }

  .deco { position: absolute; inset: 0; width: 100%; height: 100%; }

  .wordmark {
    position: absolute; left: 0; right: 0; top: 74px; text-align: center;
    font-family: "Cinzel", serif; font-weight: 500; font-size: 34px; letter-spacing: 5px; color: var(--gold);
  }
  .since {
    position: absolute; left: 0; right: 0; top: 118px; text-align: center;
    font-family: "Montserrat", sans-serif; font-size: 9px; letter-spacing: 5px; color: var(--gold);
  }
  .frame { position: absolute; inset: 12px; border: 1px solid var(--gold); }

  .holder {
    position: absolute; left: 26px; top: 36px;
    font-family: "Cormorant Garamond", serif; font-weight: 600; font-size: 16px; letter-spacing: .5px; color: var(--gold);
  }
  .role {
    position: absolute; left: 26px; top: 58px;
    font-family: "Montserrat", sans-serif; font-size: 10px; color: #5b5045;
  }
  .option--dark .role, .option--dark .contact { color: var(--caption-light); }
  .rule { position: absolute; left: 26px; top: 84px; width: 40px; height: 1px; background: var(--gold); }
  .contacts { position: absolute; left: 26px; top: 104px; list-style: none; }
  .contact {
    display: flex; align-items: center; gap: 10px; height: 22px;
    font-family: "Montserrat", sans-serif; font-size: 10px; color: #4d4338;
  }
  .contact svg { width: 11px; height: 11px; flex: none; }
  .divider { position: absolute; left: 228px; top: 30px; width: 1px; height: 140px; background: var(--gold); }
  .brand-block { position: absolute; left: 229px; right: 0; top: 66px; text-align: center; }
  .brand-dot { display: block; width: 14px; height: 14px; margin: 0 auto 8px; border-radius: 50%; background: var(--gold); }
  .brand-name { font-family: "Cinzel", serif; font-weight: 500; font-size: 15px; letter-spacing: 2px; color: var(--gold); }
  .brand-since { font-family: "Montserrat", sans-serif; font-size: 6px; letter-spacing: 2px; color: var(--gold); margin-top: 3px; }

  .caption { position: absolute; left: 0; right: 0; top: 756px; text-align: center; color: var(--caption); }
  .option--dark .caption { color: #2a2622; }
  .caption-title { font-family: "Cinzel", serif; font-size: 17px; letter-spacing: 4px; }
  .caption-rule { width: 40px; height: 1px; background: var(--gold); margin: 10px auto 18px; }
  .caption-sub { font-family: "Montserrat", sans-serif; font-size: 12px; letter-spacing: 5px; }
</style>
</head>
<body>
<main class="board">

  <!-- Option 1 -->
  <section class="option option--minimal">
    <article class="card card--front">
      <div class="wordmark">TALMORK</div>
      <div class="since">SINCE 2026</div>
    </article>
    <article class="card card--back">
      <svg class="deco" viewBox="0 0 340 200" preserveAspectRatio="none" aria-hidden="true">
        <path d="M340 120 C320 170 270 190 230 200 L340 200 Z" fill="var(--gold-light)"/>
      </svg>
      <div class="holder">TALMORK BRENNVIK</div>
      <div class="role">CEO &amp; Founder</div>
      <div class="rule"></div>
      <ul class="contacts">
        <li class="contact"><svg viewBox="0 0 12 12"><rect x="3" y="1" width="6" height="10" rx="1" fill="none" stroke="var(--gold)"/></svg>004791234567</li>
        <li class="contact"><svg viewBox="0 0 12 12"><rect x="1" y="3" width="10" height="7" fill="var(--gold)"/><path d="M1 3 L6 7 L11 3" stroke="#fff" fill="none"/></svg>talmork.llc@mailbox.com</li>
        <li class="contact"><svg viewBox="0 0 12 12"><circle cx="6" cy="6" r="5" fill="none" stroke="var(--gold)"/><path d="M1 6 H11 M6 1 C3 4 3 8 6 11 C9 8 9 4 6 1" fill="none" stroke="var(--gold)"/></svg>www.talmork.llc</li>
      </ul>
      <div class="divider"></div>
      <div class="brand-block"><span class="brand-dot"></span><div class="brand-name">TALMORK</div><div class="brand-since">SINCE 2026</div></div>
    </article>
    <div class="caption"><div class="caption-title">OPTION 1</div><div class="caption-rule"></div><div class="caption-sub">MINIMAL LUXURY</div></div>
  </section>

  <!-- Option 2 -->
  <section class="option option--dark">
    <article class="card card--front">
      <div class="frame"></div>
      <div class="wordmark">TALMORK</div>
      <div class="since">SINCE 2026</div>
    </article>
    <article class="card card--back">
      <div class="holder">TALMORK BRENNVIK</div>
      <div class="role">CEO &amp; Founder</div>
      <div class="rule"></div>
      <ul class="contacts">
        <li class="contact"><svg viewBox="0 0 12 12"><rect x="3" y="1" width="6" height="10" rx="1" fill="none" stroke="var(--gold)"/></svg>004791234567</li>
        <li class="contact"><svg viewBox="0 0 12 12"><rect x="1" y="3" width="10" height="7" fill="var(--gold)"/><path d="M1 3 L6 7 L11 3" stroke="var(--ink-dark)" fill="none"/></svg>talmork.llc@mailbox.com</li>
        <li class="contact"><svg viewBox="0 0 12 12"><circle cx="6" cy="6" r="5" fill="none" stroke="var(--gold)"/><path d="M1 6 H11 M6 1 C3 4 3 8 6 11 C9 8 9 4 6 1" fill="none" stroke="var(--gold)"/></svg>www.talmork.llc</li>
      </ul>
      <div class="divider"></div>
      <div class="brand-block"><span class="brand-dot"></span><div class="brand-name">TALMORK</div><div class="brand-since">SINCE 2026</div></div>
    </article>
    <div class="caption"><div class="caption-title">OPTION 2</div><div class="caption-rule"></div><div class="caption-sub">DARK &amp; SOPHISTICATED</div></div>
  </section>

  <!-- Option 3 -->
  <section class="option option--modern">
    <article class="card card--front">
      <svg class="deco" viewBox="0 0 320 196" preserveAspectRatio="none" aria-hidden="true">
        <path d="M0 0 H120 C90 30 60 60 70 110 C78 150 40 180 0 196 Z" fill="var(--accent-sand)"/>
        <path d="M320 40 C280 70 270 110 290 150 C300 170 290 185 270 196 H320 Z" fill="var(--accent-sand)"/>
        <path d="M130 0 C80 40 40 80 20 140" fill="none" stroke="var(--gold)" stroke-width=".8"/>
        <path d="M320 20 C270 60 260 120 230 196" fill="none" stroke="var(--gold)" stroke-width=".8"/>
      </svg>
      <div class="wordmark">TALMORK</div>
      <div class="since">SINCE 2026</div>
    </article>
    <article class="card card--back">
      <svg class="deco" viewBox="0 0 340 200" preserveAspectRatio="none" aria-hidden="true">
        <path d="M340 110 C310 140 300 175 260 200 H340 Z" fill="var(--accent-sand)"/>
        <path d="M340 90 C300 130 290 170 240 200" fill="none" stroke="var(--gold)" stroke-width=".8"/>
      </svg>
      <div class="holder">TALMORK BRENNVIK</div>
      <div class="role">CEO &amp; Founder</div>
      <div class="rule"></div>
      <ul class="contacts">
        <li class="contact"><svg viewBox="0 0 12 12"><rect x="3" y="1" width="6" height="10" rx="1" fill="none" stroke="var(--gold)"/></svg>004791234567</li>
        <li class="contact"><svg viewBox="0 0 12 12"><rect x="1" y="3" width="10" height="7" fill="var(--gold)"/><path d="M1 3 L6 7 L11 3" stroke="#fff" fill="none"/></svg>talmork.llc@mailbox.com</li>
        <li class="contact"><svg viewBox="0 0 12 12"><circle cx="6" cy="6" r="5" fill="none" stroke="var(--gold)"/><path d="M1 6 H11 M6 1 C3 4 3 8 6 11 C9 8 9 4 6 1" fill="none" stroke="var(--gold)"/></svg>www.talmork.llc</li>
      </ul>
      <div class="divider"></div>
      <div class="brand-block"><span class="brand-dot"></span><div class="brand-name">TALMORK</div><div class="brand-since">SINCE 2026</div></div>
    </article>
    <div class="caption"><div class="caption-title">OPTION 3</div><div class="caption-rule"></div><div class="caption-sub">MODERN ELEGANT</div></div>
  </section>

</main>
</body>
</html>
```